A clean crisp business card for a Landscape Construction company. Designed to be easy to read contact/ info and also be appealing/interesting, unlike a traditional business card.

Industry/Entity Type

Landscape Construction

Contact Information for Business Card

Company name : Brambleford Landscape Construction, phone number: (877) 62Vista, website:Bramblefordyards.example, Email, sales@bramblefordyards.example

Requirements
Nice to have
• Luxurious finishes/ details…. Icons or emblems next to contact info
Should not have
• Clipart or general pictures

```html
<!DOCTYPE html>
<html lang="en">
<head>
<meta charset="utf-8">
<title>Brambleford Landscape Construction – Business Card</title>
<link href="https://fonts.googleapis.com/css2?family=Cinzel:wght@600&family=Open+Sans:wght@400;600&display=swap" rel="stylesheet">
<style>
  :root {
    --bg: #c9c9c9;
    --paper: #ffffff;
    --brand-blue: #1a63b8;
    --card-blue: #2a77c8;
    --card-blue-dark: #1560b4;
    --leaf-green: #8cc63f;
    --ink: #222222;
    --ink-soft: #444444;
  }
  * { margin: 0; padding: 0; box-sizing: border-box; }
  html, body { width: 1200px; height: 675px; overflow: hidden; }
  body {
    background: var(--bg);
    font-family: "Open Sans", Arial, sans-serif;
    position: relative;
  }
  .card {
    position: absolute;
    top: 189px;
    width: 520px;
    height: 297px;
    border-radius: 16px;
    overflow: hidden;
    box-shadow: 0 10px 26px rgba(0,0,0,0.22);
  }
  .card--front { left: 45px; background: var(--paper); }
  .card--back {
    left: 635px;
    background: linear-gradient(135deg, var(--card-blue-dark), var(--card-blue) 60%, #3a84d0);
    display: flex;
    flex-direction: column;
    align-items: center;
    justify-content: center;
  }
  .accent-area {
    position: absolute;
    left: 56px;
    top: 122px;
    width: 330px;
    height: 90px;
    border-radius: 10px;
    background: linear-gradient(180deg, rgba(140,198,63,0.28), rgba(26,99,184,0.22));
  }
  .brand {
    position: absolute;
    left: 44px;
    top: 56px;
    color: var(--brand-blue);
    font-weight: 600;
    line-height: 1.1;
  }
  .brand__name { font-size: 30px; letter-spacing: 0.5px; }
  .brand__tag { font-size: 12px; letter-spacing: 3.2px; text-transform: uppercase; }
  .holder {
    position: absolute;
    right: 40px;
    top: 108px;
    text-align: right;
  }
  .holder__name {
    font-family: "Cinzel", Georgia, serif;
    font-weight: 600;
    font-size: 20px;
    color: var(--brand-blue);
  }
  .holder__role { font-size: 11px; color: var(--ink-soft); }
  .contact {
    position: absolute;
    display: flex;
    align-items: center;
    gap: 6px;
    font-size: 13px;
    color: var(--ink);
  }
  .contact svg { flex: none; }
  .contact--phone { left: 34px; top: 234px; }
  .contact--web { left: 206px; top: 234px; }
  .contact--mail { left: 206px; top: 256px; }
  .back-brand {
    color: #ffffff;
    font-weight: 600;
    text-align: center;
    line-height: 1.15;
  }
  .back-brand__name { font-size: 34px; }
  .back-brand__tag { font-size: 13px; letter-spacing: 3.5px; text-transform: uppercase; }
</style>
</head>
<body>
  <section class="card card--front">
    <div class="accent-area" role="img" aria-label="Decorative green and blue sweeping accent"></div>
    <div class="brand">
      <div class="brand__name">Brambleford</div>
      <div class="brand__tag">Landscape Construction</div>
    </div>
    <div class="holder">
      <div class="holder__name">NAME</div>
      <div class="holder__role">Owner</div>
    </div>
    <div class="contact contact--phone">
      <svg width="14" height="14" viewBox="0 0 14 14" aria-hidden="true"><circle cx="7" cy="7" r="7" fill="var(--leaf-green)"/><path d="M4.3 3.6 5.6 3.4 6.3 5.1 5.5 5.7C6 6.7 7.2 7.9 8.2 8.4L8.8 7.6 10.5 8.3 10.3 9.6C7.4 10 3.9 6.5 4.3 3.6Z" fill="#fff"/></svg>
      <span>(877) 62Vista</span>
    </div>
    <div class="contact contact--web">
      <svg width="14" height="14" viewBox="0 0 14 14" aria-hidden="true"><circle cx="7" cy="7" r="7" fill="var(--leaf-green)"/><circle cx="7" cy="7" r="4" fill="none" stroke="#fff" stroke-width="1"/><path d="M3 7H11M7 3C5.5 5 5.5 9 7 11M7 3C8.5 5 8.5 9 7 11" fill="none" stroke="#fff" stroke-width="0.9"/></svg>
      <span>www.bramblefordyards.example</span>
    </div>
    <div class="contact contact--mail">
      <svg width="14" height="14" viewBox="0 0 14 14" aria-hidden="true"><circle cx="7" cy="7" r="7" fill="var(--leaf-green)"/><rect x="3.5" y="4.5" width="7" height="5" fill="#fff"/><path d="M3.5 4.5 7 7.5 10.5 4.5" fill="none" stroke="var(--leaf-green)" stroke-width="0.9"/></svg>
      <span>sales@bramblefordyards.example</span>
    </div>
  </section>

  <section class="card card--back">
    <div class="back-brand">
      <div class="back-brand__name">Brambleford</div>
      <div class="back-brand__tag">Landscape Construction</div>
    </div>
  </section>
</body>
</html>
```